Water Management Company Letterhead

Looking for a eye-catching design of letterhead for a California based parent company of water management products. The letterhead would need to include the three logos of the sub-companies, with "The Brookline Collective LLC" (parent company) being the primary focus. Please include the sub-company logos in the following order of significance: Velmoro, Drifting Reeds North, and then Gromtile NE. The color schemes should convey water/enviornment - blues and greens. Most importantly it should be something that will stand out. All logos are uploaded. Thank you for your interest!

Target Market(s)

Environmental conservationists, government agencies, etc.

Industry/Entity Type

Environment

Font styles to use
Serif
Sans Serif

Colors
33a6d7
3276b5
abd037
cadf82
85cae6
85acd3

Requirements
Must have
• eye-catching, blue and green tones pulled from logos, water droplet.

```html
<!DOCTYPE html>
<html lang="en">
<head>
<meta charset="UTF-8">
<title>The Brookline Collective LLC – Letterhead</title>
<link href="https://fonts.googleapis.com/css2?family=Cinzel:wght@400;600&family=Open+Sans:wght@400;700&display=swap" rel="stylesheet">
<style>
  :root {
    --backdrop: #e4e5e7;
    --paper: #ffffff;
    --ink: #1f1f1f;
    --ink-soft: #3a3a3a;
    --blue-deep: #2a88c4;
    --blue-bright: #33a6d7;
    --blue-mid: #3276b5;
    --green: #8dc63f;
    --green-soft: #abd037;
    --watermark: #f0f0f0;
  }
  * { box-sizing: border-box; margin: 0; padding: 0; }
  html, body { width: 1200px; height: 1000px; overflow: hidden; }
  body {
    background: var(--backdrop);
    font-family: "Open Sans", Arial, sans-serif;
    color: var(--ink);
  }
  .letterhead {
    position: absolute;
    left: 260px; top: 50px;
    width: 680px; height: 900px;
    background: var(--paper);
    box-shadow: 0 8px 30px rgba(0,0,0,0.15);
    overflow: hidden;
  }
  .watermark {
    position: absolute;
    left: 300px; top: 330px;
    width: 300px; height: 300px;
    border-radius: 50%;
    background: var(--watermark);
  }
  .masthead {
    position: absolute;
    left: 50px; top: 50px; right: 50px;
    display: flex; justify-content: space-between;
  }
  .brand-name {
    font-family: "Cinzel", Georgia, serif;
    font-size: 34px; font-weight: 600;
    color: var(--ink-soft);
    display: flex; align-items: center; gap: 10px;
    letter-spacing: 0.5px;
  }
  .brand-dot {
    width: 16px; height: 16px; border-radius: 50%;
    background: var(--blue-bright);
  }
  .subsidiaries {
    display: flex; gap: 34px; margin-top: 12px; padding-left: 90px;
  }
  .subsidiary {
    display: flex; align-items: center; gap: 6px;
    font-size: 12px; color: var(--blue-mid);
  }
  .subsidiary .mark { width: 10px; height: 10px; border-radius: 50%; background: var(--blue-bright); }
  .subsidiary.reeds .mark { background: var(--green); }
  .subsidiary.gromtile .mark { border-radius: 0; background: var(--blue-mid); }
  .contact { list-style: none; font-size: 9.5px; line-height: 1.45; color: var(--ink-soft); }
  .contact li { display: flex; align-items: center; gap: 6px; }
  .contact .icon {
    width: 11px; height: 11px; background: var(--blue-mid);
    display: inline-flex; align-items: center; justify-content: center;
  }
  .contact .address { padding-left: 17px; }
  .recipient {
    position: absolute; left: 80px; top: 210px;
    font-size: 12px; font-weight: 700; line-height: 1.6;
  }
  .body-copy {
    position: absolute; left: 80px; top: 300px; width: 520px;
    font-size: 12px; line-height: 1.65; color: var(--ink-soft);
  }
  .body-copy p { margin-bottom: 22px; }
  .signoff { position: absolute; left: 80px; top: 640px; font-size: 12px; color: var(--ink-soft); }
  .signature {
    width: 150px; height: 46px; margin: 8px 0 6px 20px;
    background: linear-gradient(90deg, #f2f2f2, #e6e6e6);
    border-radius: 4px;
  }
  .waves { position: absolute; left: 0; bottom: 0; width: 680px; height: 260px; }
</style>
</head>
<body>
  <main class="letterhead">
    <div class="watermark" aria-hidden="true"></div>

    <header class="masthead">
      <div>
        <div class="brand-name"><span class="brand-dot"></span>The Brookline Collective LLC</div>
        <div class="subsidiaries">
          <span class="subsidiary velmoro"><span class="mark"></span>Velmoro</span>
          <span class="subsidiary reeds"><span class="mark"></span>Drifting Reeds North</span>
          <span class="subsidiary gromtile"><span class="mark"></span>Gromtile NE</span>
        </div>
      </div>
      <ul class="contact">
        <li><span class="icon"><svg width="7" height="7" viewBox="0 0 10 10"><path d="M2 1l2 2-1 1.5c.8 1.5 1.5 2.2 3 3L7.5 6l2 2-1.5 1.5C4 9 1 6 .5 2.5z" fill="#fff"/></svg></span>(000) 300-3000</li>
        <li><span class="icon"><svg width="7" height="6" viewBox="0 0 10 8"><rect x=".5" y=".5" width="9" height="7" fill="none" stroke="#fff"/><path d="M.5.5L5 4.5 9.5.5" fill="none" stroke="#fff"/></svg></span>sales@brooklinecollective.com</li>
        <li><span class="icon"><svg width="7" height="7" viewBox="0 0 10 10"><circle cx="5" cy="5" r="4" fill="none" stroke="#fff"/><path d="M1 5h8M5 1v8" stroke="#fff"/></svg></span>www.brooklinecollective.com</li>
        <li><span class="icon"><svg width="6" height="8" viewBox="0 0 8 10"><path d="M4 10S0 5.5 0 3.8a4 4 0 018 0C8 5.5 4 10 4 10z" fill="#fff"/></svg></span>Address Line 1</li>
        <li class="address">Area Name Larkvale, CA 90000</li>
      </ul>
    </header>

    <div class="recipient">
      To<br>
      Lorem Ipsum is simply<br>
      Lorem Ipsum is Lorem Ipsum is<br>
      Lorem Ipsum is
    </div>

    <section class="body-copy">
      <p>dummy text of the printing and typesetting industry. Lorem Ipsum has been the industry's standard dummy text ever since the 1500s, when an unknown printer took a galley of type and scrambled it to make a type specimen book. It has survived not only five centuries, but also the leap into electronic typesetting, remaining essentially unchanged.</p>
      <p>It is a long established fact that a reader will be distracted by the readable content of a page when looking at its layout. The point of using Lorem Ipsum is that it has a more-or-less normal distribution of letters, as opposed to using 'Content here, content here', making it look like readable English. Many desktop publishing packages and web page editors now use Lorem Ipsum as their default model text, and a search for 'lorem'.</p>
      <p>Contrary to popular belief, Lorem Ipsum is not simply random text. It has roots in a piece of classical Latin literature from 45 BC, making it over 2000 years old. Martin Halloway, a Latin professor at Ashgrove College in Virginia, looked up one of the more obscure Latin words, consectetur, from a Lorem Ipsum passage.</p>
    </section>

    <div class="signoff">
      Lorem Ipsum
      <div class="signature" role="img" aria-label="Handwritten signature"></div>
      Lorem Ipsum is a dummy
    </div>

    <svg class="waves" viewBox="0 0 680 260" preserveAspectRatio="none" aria-hidden="true">
      <path d="M0 230 C180 200 330 170 470 100 C570 50 630 20 680 10 L680 260 L0 260 Z" fill="var(--blue-deep)"/>
      <path d="M0 240 C190 215 340 185 480 120 C580 72 640 42 680 32 L680 260 L0 260 Z" fill="var(--paper)"/>
      <path d="M330 260 C420 220 500 160 580 105 C625 75 660 58 680 52 L680 260 Z" fill="var(--green)"/>
      <path d="M0 250 C200 235 360 215 500 165 C590 130 645 110 680 100 L680 112 C640 124 590 145 500 180 C360 232 200 252 0 262 Z" fill="var(--paper)"/>
    </svg>
  </main>
</body>
</html>
```